Cruise Booking Website

Cruise search and booking website

This project is a redesign of a cruise booking website we did a few years ago.

The current website is located here: http://voyage.pylonworks.example/en/

It's not fully functional but gives you ad idea how miserable the old design was.

All the information about cruises, cruise lines, destinations, ports and shore excursions will be similar to http://www.sailquest.example/
Actual search pages (form, results, single result, sailing and cabin selection, ship info, booking) will have EXACTLY the same info as sailquest.example

We like the style of http://harborfleetdesk.example, it's quite modern, good spacing, not overloaded with information. So you can use it as an example of what we like, not what we want as a final result for us. Please, don't copy it. The result should not be possible to resemble the harborfleetdesk.example, because our site has to be unique. This is important!
If you submit a design that clearly reminds another cruise site it will be rejected!

Also the mockup provided is just to give you the basic structure and show what information has to be present on the page. It doesn't mean the layout has to be the same as a mockup. The layout is up to the designer.

I've updated the mockup to be more generic so it doesn't confuse you:
https://files.boxvault.example/s/k7m2qp9wz4hx/Home%20page.png

When you're adding social sharing icons like plazanet/chirpline you have to use chinese ones instead:
https://files.boxvault.example/s/t3nr8vx5lc2e/chinese-social-icons.png
Originals: http://minilk.example/qR7t

We'll start with home page first and after it's approved inner pages can be designed.

I know the cost of the project doesn't look high, but the task is straight forward and doesn't require to be very original, it's better to follow existing design and layout patterns that proved to work well.
That's why I encourage you to choose a template to build the design on top of one of https://themeparlor.example/ themes if it will save the design work, will be easier and faster for you. So it will be more like a customization than a new design from scratch.

Mockups, site map and logo files:
- https://files.boxvault.example/sh/h48dm2rs73fkpw/QvnbW2Xz8e

Website tree:
- https://sheets.papernest.example/document/d/7xPqR2mLw9sTk4VbN8cHj3YzA6eUf5GdKo1iMnBv/edit?usp=sharing
Updates

So far a lot of designs are just copying http://www.harborfleetdesk.example/ - we don't like it!

We like the style of harborfleetdesk.example, it's quite modern, good spacing, not overloaded with information. So you can use it as an example of what we like, not what we want as a final result for us. Please, don't copy it. The result should not be possible to resemble the harborfleetdesk.example, because our site has to be unique. This is important!

Target Market(s)

Chinese travellers

Industry/Entity Type

Build

Requirements
Must have
• * White, blue and red
* Large spacing, not too much information cramped into a small space like sailquest.example or the current website
* More "hidden" info in popups, tabs and so on, so not to many things are visible at the same time
* Compatible with kestrel scaffold styling (for easier coding):
- http://kestrelkit.codeshelf.example/scaffold/index.html
- http://skinmarket.example/
* Feel free to propose to build the design on top of one of https://themeparlor.example/ themes if it will save the design work, will be easier and faster for you

```html
<!DOCTYPE html>
<html lang="en">
<head>
<meta charset="utf-8">
<title>Tidevoy – Cruise Booking</title>
<link href="https://fonts.googleapis.com/css2?family=Source+Sans+3:ital,wght@0,400;0,600;0,700;1,600;1,700&display=swap" rel="stylesheet">
<style>
:root{
  --blue:#1f6fb2;
  --blue-dark:#1a5a93;
  --nav-top:#2f8fd6;
  --nav-bottom:#1468b5;
  --nav-active:#38b4ee;
  --panel:#0d1c2b;
  --orange:#f7941d;
  --orange-dark:#e8750c;
  --red-orange:#f25c05;
  --footer:#3a78ae;
  --footer-bottom:#346c9e;
  --text:#333;
  --muted:#777;
  --line:#d8d8d8;
  --tick:#58b52f;
}
*{box-sizing:border-box;margin:0;padding:0}
html,body{width:1161px;height:1200px;overflow:hidden}
body{
  font-family:"Source Sans 3",sans-serif;color:var(--text);
  background:radial-gradient(ellipse 60% 70% at 50% 45%,#ffffff 0%,#d7e8f5 35%,#5d9ad0 70%,#2d6cab 100%);
  position:relative;
}
.page{position:absolute;left:174px;top:0;width:812px;height:1200px;background:#fff}
.abs{position:absolute}

/* header */
.logo{left:12px;top:34px;display:flex;align-items:center;gap:8px}
.logo-mark{width:40px;height:40px;border-radius:50%;background:var(--blue)}
.logo-name{font-size:32px;font-weight:700;color:var(--blue);letter-spacing:-.5px}
.account{left:594px;top:15px;font-size:11px;color:var(--blue)}
.account span{margin:0 8px;color:#888}
.social{left:700px;top:12px;font-size:10px;font-weight:600;color:#d6301f;display:flex;gap:6px}
.search{left:431px;top:63px;width:191px;height:22px;border:1px solid #ccc;border-radius:2px;background:linear-gradient(#f4f4f4,#fff);font-size:8px;color:#888;padding:6px 9px}
.search svg{position:absolute;right:7px;top:5px}
.phone{left:638px;top:47px;width:158px;height:53px;border:1px solid #ddd;display:flex;align-items:center;padding-left:9px;gap:8px}
.phone-num{font-size:18px;font-weight:700;color:var(--blue);line-height:1}
.phone-sub{font-size:14px;color:#333;line-height:1.3}

/* nav */
.nav{left:0;top:108px;width:812px;height:33px;background:linear-gradient(var(--nav-top),var(--nav-bottom));display:flex}
.nav a{color:#fff;font-size:10px;font-weight:700;text-decoration:none;display:flex;align-items:center;justify-content:center;border-right:1px solid rgba(255,255,255,.18)}
.nav a.active{background:var(--nav-active)}
.nav a:last-child{border-right:0}

/* hero */
.hero{left:0;top:141px;width:812px;height:414px;background:linear-gradient(180deg,#3f8cd6 0%,#8bc1ec 45%,#d8e6ea 65%,#8fa75a 100%)}
.hero-text{left:344px;top:353px;color:#fff;font-style:italic;font-weight:700;line-height:1.25;text-shadow:0 1px 3px rgba(0,0,0,.25)}
.hero-text .l1{font-size:22px;font-weight:600}
.hero-text .l2{font-size:28px;letter-spacing:-.5px}
.dots{left:751px;top:387px;display:flex;gap:3px}
.dots i{width:10px;height:10px;border-radius:50%;background:#fff}

.finder{left:558px;top:36px;width:238px;height:337px;background:rgba(10,22,34,.95);border-radius:2px;color:#fff;padding:0 20px}
.finder h2{font-size:21px;font-weight:400;padding:15px 0 6px;border-bottom:1px solid #2e3c4a;margin:0 -20px 10px;padding-left:21px}
.finder label{display:block;font-size:11px;margin-bottom:3px}
.sel{height:21px;background:linear-gradient(#f3f3f3,#d7d7d7);border-radius:2px;font-size:8px;color:#222;padding:5px 9px;position:relative;margin-bottom:8px}
.sel::after{content:"";position:absolute;right:0;top:0;width:18px;height:21px;border-left:1px solid #bbb}
.sel::before{content:"";position:absolute;right:5px;top:6px;border:3px solid transparent;border-bottom-color:#777;border-width:0 3px 3px}
.row{display:flex;gap:19px}
.row>div{flex:1}
.finder .big{font-size:12px;margin:4px 0 6px}
.check{font-size:9px;display:flex;align-items:center;gap:4px;margin:-2px 0 12px}
.check i{width:11px;height:11px;background:#e5e5e5;border-radius:2px}
.btn-search{height:32px;border-radius:2px;background:linear-gradient(#fdb03b,var(--orange-dark));font-size:14px;font-weight:600;display:flex;align-items:center;justify-content:center}

/* tabs */
.tabs{left:13px;top:574px;display:flex;height:31px}
.tab{height:31px;background:#666;color:#ddd;font-size:11px;display:flex;align-items:center;padding:0 22px 0 26px;margin-right:-4px;clip-path:polygon(0 0,88% 0,100% 100%,0 100%)}
.tab.active{background:linear-gradient(#79c8ee,#4fb0e0);color:#1b4e77;padding-left:20px}
.tab-box{left:13px;top:605px;width:585px;height:251px;border:1px solid var(--line)}
.tab-photo{position:absolute;left:19px;top:26px;width:306px;height:196px;border:4px solid #ddd;background:linear-gradient(180deg,#8fd0f2 0%,#2aa3d3 45%,#1c8bbd 70%,#f2efe9 100%)}
.tab-copy{position:absolute;left:351px;top:24px;width:220px}
.tab-copy h3{font-size:23px;font-weight:700;color:var(--blue);line-height:1.1}
.tab-copy .sub{font-size:14px;margin:6px 0 10px}
.tab-copy .lead{font-size:14px;color:var(--blue);line-height:1.3;margin-bottom:12px}
.tab-copy ul{list-style:none;font-size:8.5px}
.tab-copy li{display:flex;align-items:center;gap:6px;height:22px}

.news{left:628px;top:570px;width:178px;height:286px;border:1px solid var(--line);padding:12px 12px 0}
.news-photo{width:154px;height:131px;background:linear-gradient(180deg,#2c6fa9 0%,#1a3f66 55%,#0f2a45 100%)}
.news h4{font-size:12px;font-weight:700;color:var(--blue);margin-top:13px}
.news p{font-size:12px;color:var(--blue);line-height:1.5}
.email{height:21px;border:1px solid #ccc;border-radius:2px;font-size:9px;color:#888;padding:4px 9px;margin:9px 0 11px}
.btn-sub{width:85px;height:21px;border-radius:2px;background:linear-gradient(#ff7a1a,var(--red-orange));color:#fff;font-size:9px;display:flex;align-items:center;justify-content:center}

/* partners */
.partners-h{left:14px;top:879px;font-size:15px;font-weight:700;color:var(--blue)}
.arrows{left:760px;top:881px;display:flex;gap:3px}
.arrows i{width:16px;height:16px;background:#ddd;display:flex;align-items:center;justify-content:center}
.partner{top:911px;width:120px;height:60px;border:1px solid var(--line);display:flex;align-items:center;justify-content:center}
.badge{width:70px;height:20px;border-radius:3px;opacity:.85}

/* footer */
.footer{left:0;top:974px;width:812px;height:184px;background:var(--footer);color:#fff}
.col{position:absolute;top:0}
.col h5{font-size:13px;font-weight:700;margin:32px 0 8px}
.col ul{list-style:none;font-size:9px;line-height:18.3px}
.about-logo{position:absolute;left:0;top:61px;width:82px;height:80px;background:#fff;display:flex;flex-direction:column;align-items:center;justify-content:center;gap:5px}
.about-logo i{width:30px;height:30px;border-radius:50%;background:var(--blue)}
.about-logo span{font-size:10px;font-weight:700;color:var(--blue)}
.about-text{position:absolute;left:99px;top:65px;font-size:10px;line-height:15px;width:110px}
.contact p{font-size:10.5px;line-height:16px}
.contact .ci{display:flex;align-items:center;gap:6px;margin-top:5px;font-size:10px}
.bottom{left:0;top:1158px;width:812px;height:42px;background:var(--footer-bottom);color:#fff;font-size:8px;display:flex;align-items:center;justify-content:center}
</style>
</head>
<body>
<div class="page">
  <header>
    <div class="abs logo"><span class="logo-mark"></span><span class="logo-name">Tidevoy</span></div>
    <div class="abs account">Sign in<span>|</span>Signup</div>
    <div class="abs social">Pulse · Chatter · Tell · Ping</div>
    <div class="abs search">SEARCH :
      <svg width="11" height="11" viewBox="0 0 11 11"><circle cx="4.5" cy="4.5" r="3.5" fill="none" stroke="#bbb" stroke-width="1.3"/><line x1="7" y1="7" x2="10" y2="10" stroke="#bbb" stroke-width="1.5"/></svg>
    </div>
    <div class="abs phone">
      <svg width="29" height="29" viewBox="0 0 29 29"><circle cx="14.5" cy="14.5" r="13.5" fill="none" stroke="#888" stroke-width="1.3"/><path d="M10 8c-2 2-1 6 2 9s7 4 9 2l-2.5-2.5-2 1c-1.5-.6-3.4-2.5-4-4l1-2z" fill="none" stroke="#777" stroke-width="1.3"/></svg>
      <div><div class="phone-num">400 555 0199</div><div class="phone-sub">Call Us Today!</div></div>
    </div>
  </header>

  <nav class="abs nav">
    <a class="active" style="width:84px">HOME</a>
    <a style="width:117px">DESTINATIONS</a>
    <a style="width:104px">CRUISE LINES</a>
    <a style="width:106px">CRUISE INFO</a>
    <a style="width:78px">DEALS</a>
    <a style="width:128px">ONLINE BOOKING</a>
    <a style="width:103px">CONTACT US</a>
    <a style="width:92px">BLOG</a>
  </nav>

  <section class="abs hero" role="img" aria-label="Family playing happily outdoors under a bright blue sky">
    <div class="abs hero-text"><div class="l1">Cruise Vacations</div><div class="l2">&amp; So much more...</div></div>
    <form class="abs finder">
      <h2>Find Your Cruise</h2>
      <label>Destination</label>
      <div class="sel">Destination name</div>
      <div class="row">
        <div><label>Length</label><div class="sel">Length Area</div></div>
        <div><label>Month</label><div class="sel">&nbsp;</div></div>
      </div>
      <label>Cruise Lines</label>
      <div class="sel">Any Cruise line</div>
      <div class="big">Number of Travelers</div>
      <div class="row">
        <div><label>Age 25+</label><div class="sel">5</div></div>
        <div><label>Age 0 to 24</label><div class="sel">0</div></div>
      </div>
      <div class="check"><i></i>Check for senior rates</div>
      <div class="btn-search">Search Cruises</div>
    </form>
    <div class="abs dots"><i></i><i></i><i></i></div>
  </section>

  <div class="abs tabs">
    <div class="tab active">BOOK WITH US</div>
    <div class="tab">DEALS</div>
    <div class="tab">PACKAGES</div>
    <div class="tab">NEWS</div>
    <div class="tab" style="padding-right:40px">FIRST TIME CRUISER?</div>
  </div>
  <section class="abs tab-box">
    <div class="tab-photo" role="img" aria-label="Couple sitting on a white wall overlooking a turquoise sea"></div>
    <div class="tab-copy">
      <h3>BOOK WITH US!</h3>
      <p class="sub">It's easy and Fun</p>
      <p class="lead">We're most advanced cruise booking provider in china</p>
      <ul>
        <li><svg width="11" height="9" viewBox="0 0 11 9"><path d="M1 4.5l3 3L10 1" fill="none" stroke="#58b52f" stroke-width="2"/></svg>Great prices</li>
        <li><svg width="11" height="9" viewBox="0 0 11 9"><path d="M1 4.5l3 3L10 1" fill="none" stroke="#58b52f" stroke-width="2"/></svg>Fast booking processing</li>
        <li><svg width="11" height="9" viewBox="0 0 11 9"><path d="M1 4.5l3 3L10 1" fill="none" stroke="#58b52f" stroke-width="2"/></svg>20 Cruise Lines</li>
        <li><svg width="11" height="9" viewBox="0 0 11 9"><path d="M1 4.5l3 3L10 1" fill="none" stroke="#58b52f" stroke-width="2"/></svg>Destinations around the world</li>
      </ul>
    </div>
  </section>

  <aside class="abs news">
    <div class="news-photo" role="img" aria-label="White cruise ship sailing on a dark blue sea"></div>
    <h4>Cruise Deals Newsletter</h4>
    <p>Subscribe to the best deals Now!</p>
    <div class="email">Email :</div>
    <div class="btn-sub">Subscribe</div>
  </aside>

  <h3 class="abs partners-h">OUR RELIABLE PARTNERS</h3>
  <div class="abs arrows">
    <i><svg width="6" height="8"><path d="M5 0L1 4l4 4" fill="none" stroke="#fff" stroke-width="1.5"/></svg></i>
    <i><svg width="6" height="8"><path d="M1 0l4 4-4 4" fill="none" stroke="#fff" stroke-width="1.5"/></svg></i>
  </div>
  <div class="abs partner" style="left:16px"><span class="badge" style="background:#c9302c"></span></div>
  <div class="abs partner" style="left:149px"><span class="badge" style="background:#1b4aa0"></span></div>
  <div class="abs partner" style="left:282px"><span class="badge" style="background:#2d5a78"></span></div>
  <div class="abs partner" style="left:415px"><span class="badge" style="background:#f29a25"></span></div>
  <div class="abs partner" style="left:548px"><span class="badge" style="background:#45a9dc"></span></div>
  <div class="abs partner" style="left:681px"><span class="badge" style="background:#2a86c9"></span></div>

  <footer class="abs footer">
    <div class="col" style="left:27px">
      <h5>Useful Pages</h5>
      <ul><li>About Us</li><li>Contact us</li><li>Blog</li><li>FAQ</li><li>Terms of Service</li><li>Payment info</li><li>Reward Points</li></ul>
    </div>
    <div class="col" style="left:184px">
      <h5>Cruise Infov</h5>
      <ul><li>Cruise news</li><li>Visa</li><li>Honeymoon cruises</li><li>Firsttime on a Cruise</li></ul>
    </div>
    <div class="col" style="left:336px;width:230px">
      <h5 style="margin-top:36px">About tidevoy.example</h5>
      <div class="about-logo"><i></i><span>Tidevoy</span></div>
      <p class="about-text">We're the most advanced cruise booking providr in china.</p>
    </div>
    <div class="col contact" style="left:584px;width:220px">
      <h5 style="margin-top:36px">Contact Us</h5>
      <p>Marlow Harbor Studio Ltd<br>Quayside Court x118, Beacon Rd 7.2<br>Port Averly 40921 Nordmark</p>
      <div class="ci"><svg width="12" height="9" viewBox="0 0 12 9"><path d="M1 3c3-3 7-3 10 0l-2 1.5-1.5-1H4.5L3 4.5z M3 5h6l1 3H2z" fill="#fff"/></svg>(555) 010-2468 - (555)010-1357</div>
      <div class="ci"><svg width="12" height="9" viewBox="0 0 12 9"><rect x=".5" y=".5" width="11" height="8" fill="none" stroke="#fff"/><path d="M.5.5l5.5 4.5L11.5.5" fill="none" stroke="#fff"/></svg>hello@tidevoy.example</div>
    </div>
  </footer>
  <div class="abs bottom">© 2013. Tidevoy. All rights reserved.</div>
</div>
</body>
</html>
```